Business card design for my company.
I would like the card's background colour to be black. You can also see our web site to get an idea of our brand. https://www.tmwhomecrafting.com.au/
- Name
- Email

```html
<!DOCTYPE html>
<html lang="en">
<head>
<meta charset="UTF-8">
<title>TMW Home Crafting – Business Card</title>
<link rel="stylesheet" href="https://fonts.googleapis.com/css2?family=Montserrat:wght@400;500;700&display=swap">
<style>
  :root {
    --page: #2a2a2c;
    --card: #141414;
    --card-edge: #0a0a0a;
    --green: #1f9a45;
    --white: #f2f2f2;
    --muted: #d6d6d6;
    --gloss: #3a3a3a;
  }
  * { box-sizing: border-box; margin: 0; padding: 0; }
  html, body {
    width: 1200px; height: 900px; overflow: hidden;
    background: var(--page);
    font-family: "Montserrat", sans-serif;
  }
  .canvas { position: relative; width: 1200px; height: 900px; }
  .card {
    position: absolute;
    width: 560px; height: 320px;
    background: var(--card);
    border-radius: 22px;
    box-shadow: 0 6px 0 var(--card-edge), 0 20px 40px rgba(0,0,0,.45);
  }
  .card--front { left: 560px; top: 110px; }
  .card--back { left: 80px; top: 470px; }

  .brand {
    position: absolute; top: 46px; right: 48px;
    display: flex; align-items: center; gap: 12px;
  }
  .brand__mark { width: 14px; height: 14px; background: var(--green); }
  .brand__name {
    font-weight: 700; font-size: 26px; letter-spacing: 1px;
    color: var(--white); text-transform: uppercase;
  }

  .person { position: absolute; left: 40px; top: 150px; text-align: right; width: 210px; }
  .person__name { color: var(--green); font-weight: 700; font-size: 24px; }
  .person__title { color: var(--muted); font-size: 14px; margin-top: 6px; }

  .divider {
    position: absolute; left: 270px; top: 150px;
    width: 2px; height: 62px; background: var(--green);
  }

  .contact { position: absolute; left: 290px; top: 150px; list-style: none; }
  .contact li {
    display: flex; align-items: center; gap: 8px;
    color: var(--white); font-size: 14px; line-height: 21px;
  }
  .contact svg { width: 12px; height: 12px; fill: var(--white); flex: none; }

  .address {
    position: absolute; left: 40px; top: 230px; width: 460px;
    color: var(--white); font-size: 15px; text-align: center;
  }

  .back-name {
    position: absolute; inset: 0;
    display: flex; align-items: center; justify-content: center;
    font-weight: 700; font-size: 38px; letter-spacing: 2px;
    color: var(--gloss); text-transform: uppercase;
  }
</style>
</head>
<body>
<div class="canvas">
  <section class="card card--front">
    <div class="brand">
      <span class="brand__mark"></span>
      <span class="brand__name">TMW Home Crafting</span>
    </div>

    <div class="person">
      <p class="person__name">Liam Harrow</p>
      <p class="person__title">General Manager</p>
    </div>

    <div class="divider"></div>

    <ul class="contact">
      <li>
        <svg viewBox="0 0 24 24"><path d="M6.6 10.8a15 15 0 0 0 6.6 6.6l2.2-2.2c.3-.3.7-.4 1-.2 1.1.4 2.3.6 3.6.6.6 0 1 .4 1 1V20c0 .6-.4 1-1 1A17 17 0 0 1 3 4c0-.6.4-1 1-1h3.5c.6 0 1 .4 1 1 0 1.3.2 2.5.6 3.6.1.3 0 .7-.2 1z"/></svg>
        0400 555 012
      </li>
      <li>
        <svg viewBox="0 0 24 24"><path d="M2 5h20v14H2z M2 5l10 8 10-8" fill="none" stroke="#f2f2f2" stroke-width="2"/></svg>
        info@tmwhomecrafting.com.au
      </li>
      <li>
        <svg viewBox="0 0 24 24"><circle cx="12" cy="12" r="10"/></svg>
        www.tmwhomecrafting.com.au
      </li>
    </ul>

    <p class="address">Kelmore Bay, Easthaven, Australia</p>
  </section>

  <section class="card card--back">
    <p class="back-name">TMW Home Crafting</p>
  </section>
</div>
</body>
</html>
```